Wordpress website for a new Podcast

Hi, We are looking for a designer to create a wordpress website project for a new podcast and publish it on the domain we own.

The show is called “Bright Gatherings” (logo included) and its aim is to interview guests who work as professional facilitators, trainers, teachers and coaches. The show has a positive vibe, is fun, vibrant and full of positive energy. These are the feelings we want to convey in the design.

The website should have a similar structure to: https://www.plumvesselcast.example/ with the following content:

1) The main page including:
- navigation bar and social buttons at the top
- main graphic design featuring the latest episode
- "latest episodes" section displaying 3 episodes (please design a mask to be used for new episodes when they air together with the face of the interviewee) -> this will link to the respective episodes
- please design an "bright gatherings" book cover mockup to be inluded as a banner -> this will link to Orindel
- subscribe to the newsletter - a banner capturing the name and email of the user -> to be connected to PostWren.
-> a working episode search.

2) Episodes page
- the show will be divided into seasons (12 episodes each) and each episode will need a separate "blog entry" including:
-> A short article (4-5 paragraphs) + stock image
-> interviewee's bio and social links

3) Meet the hosts page
- including bios of the two hosts of the show
- links to their social profiles
- a "request speaker availability" form which sends an email

Some additional nice-to-haves:
1) Good and clean Bio's would be awesome (both for the hosts & the interviewees),
2) an easily navigable episode system,
3) a keyword/date search option
4) easy to share options (share to WhatsApp, Facebook, Twitter, LinkedIn) 5) We must be able to track how the podcasts are shared (google analytics?)

```html
<!DOCTYPE html>
<html lang="en">
<head>
<meta charset="utf-8">
<title>Bright Gatherings – Podcast</title>
<link href="https://fonts.googleapis.com/css2?family=Mulish:wght@400;600;700;800&family=Poppins:wght@600;700&display=swap" rel="stylesheet">
<style>
:root{
  --red:#f2330f;
  --orange:#f7600c;
  --yellow:#eebd1b;
  --dark:#242424;
  --ink:#222222;
  --grey:#555555;
  --light:#f4f4f4;
  --line:#e3e3e3;
  --white:#ffffff;
}
*{margin:0;padding:0;box-sizing:border-box}
html,body{width:1200px;height:3592px;overflow:hidden}
body{font-family:"Mulish",sans-serif;color:var(--ink);background:var(--white);position:relative}
.abs{position:absolute}
a{color:inherit;text-decoration:none}

/* header */
.top-bar{left:0;top:0;width:1200px;height:4px;background:var(--red)}
.social{display:flex;gap:8px}
.social span{display:block;border:2px solid #777;border-radius:50%}
.header-social{left:111px;top:54px}
.header-social span{width:36px;height:36px}
.brand-disc{border-radius:50%;background:radial-gradient(circle at 50% 45%,var(--yellow),var(--orange) 55%,var(--red) 80%);display:flex;align-items:center;justify-content:center;text-align:center}
.brand-disc b{font-family:"Poppins",sans-serif;font-weight:700;color:var(--dark);line-height:1.05}
.header-logo{left:499px;top:-72px;width:202px;height:202px;padding-top:70px}
.header-logo b{font-size:19px}
.search{left:825px;top:52px;width:263px;height:41px;border:1px solid #d6d6d6;border-radius:3px;font-size:13px;color:#666;padding:11px 16px}
.search svg{position:absolute;right:14px;top:13px}
.nav-rule{left:111px;top:143px;width:977px;height:1px;background:var(--line)}
.main-nav{left:111px;top:144px;width:977px;height:66px;display:flex;justify-content:space-around;align-items:center;font-size:13px;font-weight:600}
.main-nav a{position:relative;height:66px;line-height:66px;padding:0 8px}
.main-nav a.active{color:var(--red)}
.main-nav a.active::after{content:"";position:absolute;left:0;right:0;bottom:0;height:3px;background:var(--red)}

/* hero */
.hero{left:0;top:210px;width:1200px;height:645px;background:linear-gradient(135deg,#2b2b2b,#1f1f1f)}
.book{left:171px;top:69px;width:303px;height:534px;background:linear-gradient(160deg,var(--red),var(--orange) 55%,var(--yellow));transform:skewY(3deg);box-shadow:8px 6px 0 #f1f1f1}
.hero-copy{left:560px;top:160px;width:480px;text-align:center;color:var(--white)}
.hero-title{font-family:"Poppins",sans-serif;font-weight:700;line-height:1}
.hero-title .l1{display:block;font-size:60px;letter-spacing:3px}
.hero-title .l2{display:block;font-size:66px;color:var(--red);margin-top:10px;letter-spacing:1px}
.hero-copy p{font-size:16px;line-height:29px;margin-top:26px}
.hero-btns{display:flex;justify-content:center;gap:14px;margin-top:34px}
.btn{display:inline-block;color:var(--white);font-size:16px;text-align:center}
.hero-btns .btn{height:52px;line-height:52px;padding:0 18px}
.btn-red{background:var(--red)}
.btn-yellow{background:var(--yellow)}

/* sections */
.section-title{width:1200px;text-align:center;font-size:31px;font-weight:600;left:0}
.section-title em{font-style:normal;color:var(--red)}
.title-rule{left:573px;width:54px;height:3px;background:var(--red)}
.welcome-text{left:260px;top:996px;width:680px;text-align:center;font-size:15px;line-height:31px;color:var(--grey)}
.pill{left:498px;top:1155px;width:204px;height:62px;border-radius:31px;background:linear-gradient(90deg,var(--red),var(--yellow));color:var(--white);font-size:21px;font-weight:600;line-height:62px;text-align:center}

.episodes-band{left:0;top:1282px;width:1200px;height:708px;background:var(--light)}
.ep-card{top:1416px;width:309px;height:513px;background:var(--white);box-shadow:0 0 4px rgba(0,0,0,.12);text-align:center}
.ep-photo{width:309px;height:219px}
.ep-icon{position:absolute;left:124px;top:191px;width:61px;height:61px;border-radius:50%;background:linear-gradient(var(--red),var(--orange));display:flex;align-items:center;justify-content:center}
.ep-num{margin-top:52px;color:var(--red);font-size:17px}
.ep-title{margin-top:14px;font-size:15px;font-weight:700}
.ep-desc{margin:14px 22px 0;font-size:12px;line-height:27px;color:var(--grey)}
.ep-card .btn{position:absolute;left:25px;top:443px;width:259px;height:45px;line-height:45px}

/* hosts */
.hosts{left:0;top:1990px;width:1200px;height:505px;background:linear-gradient(90deg,#3a2418 0%,#2e1c12 45%,#4b3425 70%,#2a1a10 100%)}
.bubble{left:615px;top:37px;width:178px;height:104px;border-radius:50%;background:var(--white);display:flex;align-items:center;justify-content:center;text-align:center;font-family:"Poppins",sans-serif;font-weight:700;font-size:18px;color:var(--red);line-height:1.1}
.hosts h2{left:111px;top:128px;font-size:55px;font-weight:700;color:var(--white)}
.hosts p{left:111px;top:207px;width:520px;font-size:15px;line-height:32px;color:#eee}
.hosts .btn{left:111px;top:336px;width:171px;height:52px;line-height:52px;font-weight:700}

/* newsletter */
.news{left:0;top:2495px;width:1200px;height:373px;background:linear-gradient(90deg,var(--red) 20%,var(--orange) 55%,var(--yellow))}
.calendar{left:149px;top:46px;width:371px;height:327px;background:linear-gradient(#ffffff,#eeeeee)}
.news h2{left:569px;top:56px;font-size:44px;font-weight:700;color:var(--white)}
.news p{left:569px;top:124px;width:470px;font-size:14px;line-height:29px;color:#fff4ea}
.field{top:206px;width:226px;height:49px;background:var(--white);font-size:13px;color:#555;padding:16px 16px}
.news .btn{left:570px;top:280px;width:171px;height:52px;line-height:52px;font-size:18px;font-weight:700}

/* testimonials */
.quote{left:230px;top:2995px;width:740px;text-align:center;font-size:15px;line-height:34px;color:var(--grey)}
.quote .mark{font-family:"Poppins",sans-serif;font-weight:700;font-size:22px;color:var(--ink)}
.author{left:0;top:3113px;width:1200px;text-align:center;font-size:20px;color:var(--red)}
.posted{left:0;top:3145px;width:1200px;text-align:center;font-size:15px;color:var(--grey)}

/* footer */
.footer{left:0;top:3213px;width:1200px;height:379px;background:#161616;border-top:5px solid var(--red);overflow:hidden}
.footer-logo{left:475px;top:-46px;width:250px;height:250px;padding-top:40px}
.footer-logo b{font-size:22px}
.footer-nav{left:0;top:200px;width:1200px;text-align:center;font-size:13px;color:var(--white)}
.footer-nav a{margin:0 9px}
.footer-nav i{font-style:normal;margin:0 2px}
.footer-social{left:496px;top:261px}
.footer-social span{width:36px;height:36px;border-color:var(--white)}
.copyright{left:0;top:333px;width:1200px;text-align:center;font-size:12px;color:var(--white)}
</style>
</head>
<body>

<div class="abs top-bar"></div>
<div class="abs social header-social" aria-label="Social links"><span></span><span></span><span></span><span></span><span></span></div>
<div class="abs brand-disc header-logo"><b>Bright<br>Gatherings</b></div>
<div class="abs search">Search
  <svg width="12" height="12" viewBox="0 0 12 12"><circle cx="5" cy="5" r="3.8" fill="none" stroke="#555" stroke-width="1.6"/><line x1="8" y1="8" x2="11" y2="11" stroke="#555" stroke-width="1.6"/></svg>
</div>
<div class="abs nav-rule"></div>
<nav class="abs main-nav">
  <a class="active">Home</a><a>Episodes</a><a>Meet the hosts</a><a>About</a><a>Blog</a><a>Podcasts</a><a>Training</a><a>Contact Us</a>
</nav>

<section class="abs hero">
  <div class="abs book" role="img" aria-label="Bright Gatherings book cover mockup"></div>
  <div class="abs hero-copy">
    <h1 class="hero-title"><span class="l1">BRIGHT</span><span class="l2">GATHERINGS</span></h1>
    <p>Sed ut perspiciatis unde omnis iste natus error sit voluptatem accusantium doloremque laudantium</p>
    <div class="hero-btns"><a class="btn btn-red">Get the Book Now</a><a class="btn btn-yellow">Get Trained</a></div>
  </div>
</section>

<h2 class="abs section-title" style="top:912px">Welcome to <em>Bright Gatherings</em></h2>
<div class="abs title-rule" style="top:972px"></div>
<p class="abs welcome-text">Sed ut perspiciatis unde omnis iste natus error sit voluptatem accusantium doloremque laudantium, totam rem aperiam, eaque ipsa quae ab illo inventore veritatis et quasi architecto beatae vitae dicta sunt explicabo. Nemo enim ipsam voluptatem quia voluptas sit aspernatur aut odit aut fugit, sed quia magni dolores eos qui ratione voluptatem sequi nesciunt</p>
<a class="abs pill">Read More</a>

<div class="abs episodes-band"></div>
<h2 class="abs section-title" style="top:1325px">Latest <em>Podcast Episodes</em></h2>
<div class="abs title-rule" style="top:1385px"></div>

<article class="abs ep-card" style="left:111px">
  <div class="ep-photo" role="img" aria-label="Photo of a host interviewing a guest on a waterfront terrace" style="background:linear-gradient(#c9d3dc,#8a8f94 60%,#4a4a4a)"></div>
  <div class="ep-icon"><svg width="26" height="26" viewBox="0 0 26 26" fill="none" stroke="#fff" stroke-width="2"><circle cx="13" cy="11" r="2.5" fill="#fff"/><path d="M8 16a7 7 0 1 1 10 0"/><path d="M5 19a11 11 0 1 1 16 0"/><line x1="13" y1="14" x2="13" y2="24"/></svg></div>
  <div class="ep-num">Episode 195</div>
  <div class="ep-title">Sed ut perspiciatis unde omnis iste</div>
  <p class="ep-desc">Nemo enim ipsam voluptatem quia voluptas sit aspernatur aut odit aut fugit, sed quia consequ magni dolores eos qui ratione</p>
  <a class="btn btn-red">Read More</a>
</article>

<article class="abs ep-card" style="left:446px">
  <div class="ep-photo" role="img" aria-label="Photo of two men in conversation on a stage" style="background:linear-gradient(120deg,#3a3a3a,#1a1a1a 60%,#8a6a2a)"></div>
  <div class="ep-icon"><svg width="26" height="26" viewBox="0 0 26 26" fill="none" stroke="#fff" stroke-width="2"><circle cx="13" cy="11" r="2.5" fill="#fff"/><path d="M8 16a7 7 0 1 1 10 0"/><path d="M5 19a11 11 0 1 1 16 0"/><line x1="13" y1="14" x2="13" y2="24"/></svg></div>
  <div class="ep-num">Episode 195</div>
  <div class="ep-title">Sed ut perspiciatis unde omnis iste</div>
  <p class="ep-desc">Nemo enim ipsam voluptatem quia voluptas sit aspernatur aut odit aut fugit, sed quia consequ magni dolores eos qui ratione</p>
  <a class="btn btn-red">Read More</a>
</article>

<article class="abs ep-card" style="left:780px">
  <div class="ep-photo" role="img" aria-label="Photo of two colleagues talking at an office table" style="background:linear-gradient(#5a6270,#8c8f95 55%,#d8d2c4)"></div>
  <div class="ep-icon"><svg width="26" height="26" viewBox="0 0 26 26" fill="none" stroke="#fff" stroke-width="2"><circle cx="13" cy="11" r="2.5" fill="#fff"/><path d="M8 16a7 7 0 1 1 10 0"/><path d="M5 19a11 11 0 1 1 16 0"/><line x1="13" y1="14" x2="13" y2="24"/></svg></div>
  <div class="ep-num">Episode 195</div>
  <div class="ep-title">Sed ut perspiciatis unde omnis iste</div>
  <p class="ep-desc">Nemo enim ipsam voluptatem quia voluptas sit aspernatur aut odit aut fugit, sed quia consequ magni dolores eos qui ratione</p>
  <a class="btn btn-red">Read More</a>
</article>

<section class="abs hosts" role="img" aria-label="Photo of a smiling woman at a desk in warm evening light">
  <div class="abs bubble">Bright<br>Gatherings</div>
  <h2 class="abs">Meet The Hosts</h2>
  <p class="abs">Sed ut perspiciatis unde omnis iste natus error sit voluptatem accusanti doloremque laudantium, totam rem aperiam, eaque ipsa quae ab illo et quasi architecto beatae vitae dicta sunt explicabo.</p>
  <a class="abs btn btn-red">Register Now</a>
</section>

<section class="abs news">
  <div class="abs calendar" role="img" aria-label="Branded wall calendar showing January 2020"></div>
  <h2 class="abs">Newsletter Subscribe</h2>
  <p class="abs">Sed ut perspiciatis unde omnis iste natus error sit voluptatem acc usantium doloremque laudantium, totam</p>
  <div class="abs field" style="left:570px">First Name :</div>
  <div class="abs field" style="left:804px">Email :</div>
  <a class="abs btn btn-red">Subscribe</a>
</section>

<h2 class="abs section-title" style="top:2906px">Our <em>Testimonials</em></h2>
<div class="abs title-rule" style="top:2963px"></div>
<p class="abs quote"><span class="mark">“</span> Sed ut perspiciatis unde omnis iste natus error sit voluptatem accusantium doloremque laudantium, totam rem aperiam, eaque ipsa quae ab illo inventore veritatis et quasi architecto beatae vitae dicta sunt explicabo. quia consequuntur magni dolores eos qui ratione voluptatem sequi nesciunt. <span class="mark">”</span></p>
<div class="abs author">-Jhon Smith</div>
<div class="abs posted">Posed on 25 June 2019</div>

<footer class="abs footer">
  <div class="abs brand-disc footer-logo"><b>Bright<br>Gatherings</b></div>
  <nav class="abs footer-nav">
    <a>Home</a><i>/</i><a>Episodes</a><i>/</i><a>Meet the hosts</a><i>/</i><a>About</a><i>/</i><a>Blog</a><i>/</i><a>Podcasts</a><i>/</i><a>Training</a><i>/</i><a>Contact Us</a>
  </nav>
  <div class="abs social footer-social" aria-label="Social links"><span></span><span></span><span></span><span></span><span></span></div>
  <div class="abs copyright">© Copyright 2019 Bright Gatherings.All Rights Reserved</div>
</footer>

</body>
</html>
```